Business Card Design Project - del varosi group

dear Sirs

we need business card design for our group ( DEL Varosi Group ) , i have got the Logo design of our group from pixel harbor in previous , so all need details relating to our group i think available with you, as well as the the chosen logo design

we hope to provide us with business card logo that to be appropaite and satisfactory to us .

thanks

note : logo design of our group is attached .
Updates

Reason: please extend the deadline of my project for additional 15 days because i didn't received appropriate design for our gruop yet . kindly beaware that i have received 77 design till now , supossed to send me 200-250 design at least . thanks

Target Market(s)

contents

name : Kerem EL Nadiri

position : Operation Manager

Industry/Entity Type

Business

Requirements
Must have

• person name

group logo
Nice to have
• logo color matching with back background

```html
<!DOCTYPE html>
<html lang="en">
<head>
<meta charset="utf-8">
<title>DEL Varosi Group – Business Card</title>
<link rel="stylesheet" href="https://fonts.googleapis.com/css2?family=Open+Sans:wght@400;600&display=swap">
<style>
  :root {
    --backdrop: #efe9d6;
    --card: #ffffff;
    --navy: #1d3f86;
    --navy-deep: #132c66;
    --gold: #c9a13a;
    --gold-light: #e6c46a;
    --ink: #2b2b2b;
    --muted: #555555;
  }
  * { box-sizing: border-box; margin: 0; padding: 0; }
  html, body { width: 1200px; height: 951px; overflow: hidden; }
  body {
    background: var(--backdrop);
    font-family: "Open Sans", Arial, sans-serif;
    color: var(--ink);
    position: relative;
  }
  .card {
    position: absolute;
    left: 250px;
    width: 700px;
    height: 400px;
    background: var(--card);
    border-radius: 22px;
    overflow: hidden;
    box-shadow: 0 4px 14px rgba(0,0,0,0.12);
  }
  .card--front { top: 25px; }
  .card--back { top: 526px; }

  .brand {
    display: flex;
    align-items: center;
    gap: 14px;
    color: var(--navy);
    font-weight: 600;
    text-transform: uppercase;
    letter-spacing: 1px;
    white-space: nowrap;
  }
  .brand__mark {
    background: var(--gold);
    flex: none;
  }

  .card--front .brand {
    position: absolute;
    top: 140px;
    left: 0; right: 0;
    justify-content: center;
    font-size: 46px;
  }
  .card--front .brand__mark { width: 40px; height: 40px; }
  .front-web {
    position: absolute;
    top: 245px;
    left: 0; right: 0;
    text-align: center;
    color: var(--gold);
    font-size: 18px;
    letter-spacing: 2px;
  }

  .card--back .brand {
    position: absolute;
    top: 42px;
    left: 50px;
    font-size: 30px;
  }
  .card--back .brand__mark { width: 26px; height: 26px; }

  .person {
    position: absolute;
    top: 78px;
    right: 50px;
    text-align: left;
  }
  .person__name { font-size: 20px; letter-spacing: 1px; color: var(--ink); }
  .person__role { font-size: 16px; color: var(--gold); font-style: normal; letter-spacing: 1px; }

  .address {
    position: absolute;
    top: 172px;
    left: 50px;
    display: flex;
    gap: 10px;
    font-style: normal;
    font-size: 17px;
    line-height: 1.3;
    color: var(--muted);
  }
  .contacts {
    position: absolute;
    top: 166px;
    left: 410px;
    list-style: none;
    font-size: 17px;
    line-height: 1.35;
    color: var(--muted);
  }
  .contacts li { display: flex; align-items: center; gap: 10px; }
  .contacts .hl { color: var(--gold); }
  .icon { width: 16px; height: 16px; flex: none; fill: var(--gold); }

  .wave { position: absolute; left: 0; bottom: 0; width: 700px; height: 140px; }
</style>
</head>
<body>

<section class="card card--front" aria-label="Card front">
  <div class="brand"><span class="brand__mark"></span>DEL Varosi Group</div>
  <p class="front-web">www.delvarosigroup.com</p>
</section>

<section class="card card--back" aria-label="Card back">
  <div class="brand"><span class="brand__mark"></span>DEL Varosi Group</div>

  <div class="person">
    <p class="person__name">Kerem EL Nadiri</p>
    <p class="person__role">Operation Manager</p>
  </div>

  <address class="address">
    <svg class="icon" viewBox="0 0 16 16" aria-hidden="true"><path d="M8 1 1 7h2v7h4v-4h2v4h4V7h2z"/></svg>
    <span>4150 Corvin Lane<br>Suite 210-380<br>Alder, TX 78115</span>
  </address>

  <ul class="contacts">
    <li><svg class="icon" viewBox="0 0 16 16" aria-hidden="true"><path d="M3 1h3l1 4-2 1c1 2 2 3 4 4l1-2 4 1v3c0 1-1 2-2 2C6 14 2 10 1 3c0-1 1-2 2-2z"/></svg>555-014-2290</li>
    <li><svg class="icon" viewBox="0 0 16 16" aria-hidden="true"><path d="M4 1h8v4H4zM1 6h14v6h-3v3H4v-3H1zm4 4v3h6v-3z"/></svg>555-014-2291</li>
    <li><svg class="icon" viewBox="0 0 16 16" aria-hidden="true"><path d="M1 3h14v10H1zm1 1 6 5 6-5z"/></svg><span>info@<span class="hl">delvarosigroup</span>.com</span></li>
    <li><svg class="icon" viewBox="0 0 16 16" aria-hidden="true"><circle cx="8" cy="8" r="7"/></svg><span>www.<span class="hl">delvarosigroup</span>.com</span></li>
  </ul>

  <svg class="wave" viewBox="0 0 700 140" preserveAspectRatio="none" aria-hidden="true">
    <defs>
      <linearGradient id="goldBand" x1="0" x2="1">
        <stop offset="0" stop-color="var(--gold)"/>
        <stop offset="0.5" stop-color="var(--gold-light)"/>
        <stop offset="1" stop-color="var(--gold)"/>
      </linearGradient>
      <linearGradient id="navyBand" x1="0" x2="1">
        <stop offset="0" stop-color="var(--navy-deep)"/>
        <stop offset="1" stop-color="var(--navy)"/>
      </linearGradient>
    </defs>
    <path d="M0 40 C180 70 380 50 700 20 L700 140 L0 140 Z" fill="url(#goldBand)"/>
    <path d="M0 58 C200 86 400 66 700 36 L700 140 L0 140 Z" fill="#ffffff"/>
    <path d="M0 66 C220 100 420 78 700 48 L700 140 L0 140 Z" fill="url(#navyBand)"/>
  </svg>
</section>

</body>
</html>
```